KRV Cartridge chip board folding ammuniton boxes for retail sale

Design a scalable design for use with 20 round and 50 round boxes for Ammunition. The caliber will be 9mm but will need to be editable, all warnings and barcodes will need to be able to be edited also. I have attached the company logo.

**UPDATE**
Box dimensions
20rd= 2.55in long X 2.1in width X 1.25in height

50rd= 5.1in long x 2.6in width X 1.2in height

Please see the bullet picture i would like used if possible.

Target Market(s)

Quality shooting sports, self defense

Industry/Entity Type

Self Defense

Requirements
Must have
• supplied company logo design
Should not have
• any cartoons of any kind

```html
<!DOCTYPE html>
<html lang="en">
<head>
<meta charset="utf-8">
<title>KRV Cartridge – 9mm 115gr Box Layout</title>
<link href="https://fonts.googleapis.com/css2?family=Montserrat:wght@900&family=Ubuntu:wght@500;700&display=swap" rel="stylesheet">
<style>
  :root {
    --stage: #eceeef;
    --panel-white: #ffffff;
    --panel-soft: #e9ebec;
    --wine-dark: #5a0a0e;
    --wine: #8c1a1d;
    --wine-muted: #5e1e20;
    --signal-red: #c8202b;
    --ink: #161a1c;
    --label-ink: #6a0f14;
    --brass-light: #e8cf86;
    --brass: #b8923e;
    --brass-dark: #7a5a1f;
  }
  * { margin: 0; padding: 0; box-sizing: border-box; }
  html, body { width: 1200px; height: 750px; overflow: hidden; background: var(--stage); }
  .canvas { position: relative; width: 1200px; height: 750px; }

  .panel {
    position: absolute; overflow: hidden;
    background: linear-gradient(180deg, var(--panel-white), var(--panel-soft));
  }
  .panel__shapes { position: absolute; inset: 0; }
  .panel--top { left: 252px; top: 68px; width: 900px; height: 170px; }
  .panel--side { left: 50px; top: 240px; width: 200px; height: 420px; }
  .panel--front { left: 252px; top: 240px; width: 900px; height: 420px; }

  .brand { position: absolute; display: flex; align-items: center; }
  .brand__name { font-family: "Ubuntu", sans-serif; font-weight: 700; color: var(--ink); white-space: nowrap; }
  .brand__mark { border-radius: 50%; border-style: solid; border-color: var(--signal-red); flex: none; }
  .brand__tagline {
    position: absolute; font-family: "Ubuntu", sans-serif; font-weight: 500;
    text-transform: uppercase; color: var(--signal-red); white-space: nowrap;
  }

  /* top panel */
  .panel--top .brand { left: 330px; top: 24px; gap: 10px; }
  .panel--top .brand__name { font-size: 26px; }
  .panel--top .brand__mark { width: 32px; height: 32px; border-width: 4px; }
  .panel--top .brand__tagline { left: 332px; top: 58px; font-size: 8px; letter-spacing: 4px; }
  .top-spec {
    position: absolute; left: 300px; top: 100px; width: 300px; text-align: center;
    font-family: "Ubuntu", sans-serif; font-weight: 500; font-size: 16px; line-height: 1.45;
    color: var(--panel-white); white-space: nowrap;
  }

  /* side panel */
  .panel--side .brand { left: 16px; top: 60px; gap: 8px; }
  .panel--side .brand__name { font-size: 20px; }
  .panel--side .brand__mark { width: 24px; height: 24px; border-width: 3px; }
  .panel--side .brand__tagline { left: 17px; top: 88px; font-size: 6px; letter-spacing: 2.5px; }
  .side-spec {
    position: absolute; left: 0; top: 318px; width: 200px; text-align: center;
    color: var(--panel-white); font-family: "Ubuntu", sans-serif; white-space: nowrap;
  }
  .side-spec__caliber { font-weight: 700; font-size: 26px; line-height: 1.2; }
  .side-spec__line { font-weight: 500; font-size: 12px; line-height: 1.4; }

  /* front panel */
  .panel--front .brand { left: 480px; top: 26px; gap: 14px; }
  .panel--front .brand__name { font-size: 40px; }
  .panel--front .brand__mark { width: 52px; height: 52px; border-width: 5px; }
  .panel--front .brand__tagline { left: 482px; top: 80px; font-size: 10px; letter-spacing: 5px; }

  .spec-table {
    position: absolute; left: 270px; top: 110px; width: 600px; height: 112px;
    display: grid; grid-template-columns: 320px 1fr; grid-template-rows: 1fr 1fr;
    border: 3px solid var(--signal-red); background: var(--panel-white);
  }
  .spec-table__caliber {
    grid-row: 1 / span 2; border-right: 3px solid var(--signal-red);
    display: flex; align-items: center; justify-content: center;
    font-family: "Ubuntu", sans-serif; font-weight: 700; font-size: 52px; color: var(--label-ink);
  }
  .spec-table__type, .spec-table__line {
    display: flex; align-items: center; justify-content: center;
    font-family: "Ubuntu", sans-serif; font-weight: 500; font-size: 20px; color: var(--label-ink); white-space: nowrap;
  }
  .spec-table__type { border-bottom: 3px solid var(--signal-red); }

  .cartridge-art {
    position: absolute; left: 100px; top: 130px; width: 120px; height: 270px;
    border-radius: 60px 60px 8px 8px;
    background: linear-gradient(90deg, var(--brass-dark), var(--brass-light) 40%, var(--brass) 75%, var(--brass-dark));
  }

  .headline {
    position: absolute; left: 270px; top: 284px;
    font-family: "Montserrat", sans-serif; font-weight: 900; font-size: 38px; line-height: 1.02;
    color: var(--panel-white); text-transform: uppercase;
  }

  .count-badge {
    position: absolute; left: 770px; top: 272px; width: 96px; height: 122px;
    border: 3px solid var(--panel-white);
    display: flex; flex-direction: column; align-items: center; justify-content: center;
    color: var(--panel-white); font-family: "Ubuntu", sans-serif; text-align: center;
  }
  .count-badge__number { font-weight: 700; font-size: 50px; line-height: 1; }
  .count-badge__label { font-weight: 500; font-size: 15px; line-height: 1.05; }
</style>
</head>
<body>
<main class="canvas">
  <svg width="0" height="0" aria-hidden="true" style="position:absolute">
    <defs>
      <linearGradient id="wine-band" x1="0" y1="0" x2="1" y2="0">
        <stop offset="0" stop-color="#5a0a0e"/>
        <stop offset="0.55" stop-color="#8c1a1d"/>
        <stop offset="1" stop-color="#5e1e20"/>
      </linearGradient>
    </defs>
  </svg>

  <section class="panel panel--top">
    <svg class="panel__shapes" width="900" height="170" viewBox="0 0 900 170" aria-hidden="true">
      <polygon points="0,170 0,150 900,60 900,170" fill="url(#wine-band)"/>
      <polygon points="0,170 0,120 260,90 620,90 900,30 900,170" fill="url(#wine-band)"/>
    </svg>
    <div class="brand">
      <span class="brand__name">KRV Cartridge</span>
      <span class="brand__mark"></span>
    </div>
    <div class="brand__tagline">Precision Made</div>
    <div class="top-spec">FULL METAL JACKET<br>FMJ / ELITE AMMUNITION</div>
  </section>

  <section class="panel panel--side">
    <svg class="panel__shapes" width="200" height="420" viewBox="0 0 200 420" aria-hidden="true">
      <polygon points="0,250 200,300 200,420 0,420" fill="url(#wine-band)"/>
    </svg>
    <div class="brand">
      <span class="brand__name">KRV Cartridge</span>
      <span class="brand__mark"></span>
    </div>
    <div class="brand__tagline">Precision Made</div>
    <div class="side-spec">
      <div class="side-spec__caliber">9mm 115gr</div>
      <div class="side-spec__line">FULL METAL JACKET</div>
      <div class="side-spec__line">FMJ / ELITE AMMUNITION</div>
    </div>
  </section>

  <section class="panel panel--front">
    <svg class="panel__shapes" width="900" height="420" viewBox="0 0 900 420" aria-hidden="true">
      <polygon points="0,0 440,0 0,60" fill="url(#wine-band)"/>
      <polygon points="0,280 900,228 900,420 0,420" fill="url(#wine-band)"/>
    </svg>

    <div class="brand">
      <span class="brand__name">KRV Cartridge</span>
      <span class="brand__mark"></span>
    </div>
    <div class="brand__tagline">Precision Made</div>

    <div class="spec-table">
      <div class="spec-table__caliber">9mm 115gr</div>
      <div class="spec-table__type">FULL METAL JACKET</div>
      <div class="spec-table__line">FMJ / ELITE AMMUNITION</div>
    </div>

    <div class="cartridge-art" role="img" aria-label="Photograph of a brass 9mm full metal jacket cartridge"></div>

    <h1 class="headline">Elite<br>Performance<br>Ammunition</h1>

    <div class="count-badge">
      <span class="count-badge__number">50</span>
      <span class="count-badge__label">Cartridge<br>per box</span>
    </div>
  </section>
</main>
</body>
</html>
```